Building company buisness cards

We are looking for a sharp modern new look for our business cards.
We are a New Zealand based company that specialises in house and land packages.
We have attached a photo of the current logo and would like to see if it can be improved somehow if needed.
We are open to any colours but we have chosen green at this stage.
Feel free to change the font and make the logo smarter looking.
Play with the colours and see what looks best.

We want a card that looks so good know one will want to throw it away!

Target Market(s)

Home buyers

Industry/Entity Type

Building

Contact Information for Business Card

Derek Tolvane
0217394062
dtolvane@quillmarkhomesteads.co.nz
quillmarkhomesteads.co.nz

Font styles to use
Serif
Sans Serif

Colors

Designer to choose colors to be used in the design.

Requirements
Must have
• Logo and company name on one side, details on the other side
Nice to have
• Color codes for the original green are HEX #4a8028, RGB(74,128,40), CMYK(42,0,69,50)
• Round corners, Raised and/or spot UV

```html
<!DOCTYPE html>
<html lang="en">
<head>
<meta charset="utf-8">
<title>Quillmark Homesteads — Business Card</title>
<link rel="stylesheet" href="https://fonts.googleapis.com/css2?family=Open+Sans:wght@300;400;700&display=swap">
<style>
  :root {
    --backdrop: #e9e6e1;
    --card-white: #f7f7f7;
    --brand-green: #14a014;
    --band-grey: #5f5f60;
    --ink: #121212;
    --on-green: #ffffff;
    --rule: #c9c9c9;
  }
  * { margin: 0; padding: 0; box-sizing: border-box; }
  html, body {
    width: 1200px; height: 1024px; overflow: hidden;
    background: var(--backdrop);
  }
  .stage {
    width: 1200px; height: 1024px;
    display: flex; align-items: center; justify-content: center;
  }
  .business-card {
    position: relative;
    width: 1000px; height: 560px;
    background: var(--card-white);
    border-radius: 14px;
    overflow: hidden;
    box-shadow: 0 12px 30px rgba(0,0,0,0.18);
    font-family: "Open Sans", Arial, sans-serif;
  }
  .card-swoosh { position: absolute; inset: 0; width: 100%; height: 100%; }
  .brand-block {
    position: absolute; left: 80px; top: 210px;
    display: flex; align-items: flex-start; gap: 18px;
  }
  .brand-square {
    width: 30px; height: 30px; margin-top: 10px;
    background: var(--brand-green);
  }
  .brand-name {
    color: var(--brand-green);
    font-weight: 700;
    font-size: 50px; line-height: 50px;
    letter-spacing: -0.5px;
  }
  .brand-name span { display: block; }
  .brand-rule {
    width: 90px; height: 1px; background: var(--rule);
    margin: 22px 0 0 110px;
  }
  .contact-block {
    position: absolute; right: 44px; top: 70px;
    text-align: right; color: var(--on-green);
  }
  .contact-name {
    color: var(--ink); font-size: 32px; font-weight: 400;
    margin-right: 56px; margin-bottom: 60px;
  }
  .contact-line {
    display: flex; justify-content: flex-end; align-items: center;
    gap: 18px; font-size: 21px; font-weight: 300; height: 36px;
  }
  .contact-line .contact-icon { width: 22px; height: 22px; flex: none; }
  .contact-line .icon-spacer { width: 22px; flex: none; }
</style>
</head>
<body>
<main class="stage">
  <article class="business-card">
    <svg class="card-swoosh" viewBox="0 0 1000 560" preserveAspectRatio="none" aria-hidden="true">
      <path d="M430 0 C 520 180, 600 360, 640 560 L1000 560 L1000 0 Z" fill="var(--band-grey)"/>
      <path d="M540 0 C 590 180, 625 360, 645 560 L1000 560 L1000 0 Z" fill="var(--brand-green)"/>
    </svg>

    <div class="brand-block">
      <div class="brand-square"></div>
      <div>
        <p class="brand-name"><span>quillmark</span><span>homesteads.</span></p>
        <div class="brand-rule"></div>
      </div>
    </div>

    <div class="contact-block">
      <p class="contact-name">Derek Tolvane</p>
      <p class="contact-line">0217394062
        <svg class="contact-icon" viewBox="0 0 22 22"><rect width="22" height="22" rx="2" fill="#fff"/><path d="M7 5l3 3-1.6 1.6a9 9 0 0 0 4 4L14 12l3 3-2 2c-5 0-10-5-10-10z" fill="var(--brand-green)"/></svg>
      </p>
      <p class="contact-line">dtolvane@quillmarkhomesteads.co.nz
        <svg class="contact-icon" viewBox="0 0 22 22"><rect width="22" height="22" rx="2" fill="#fff"/><rect x="4" y="6" width="14" height="10" fill="none" stroke="var(--brand-green)" stroke-width="1.6"/><path d="M4 6l7 6 7-6" fill="none" stroke="var(--brand-green)" stroke-width="1.6"/></svg>
      </p>
      <p class="contact-line">quillmarkhomesteads.co.nz
        <svg class="contact-icon" viewBox="0 0 22 22"><rect width="22" height="22" rx="2" fill="#fff"/><circle cx="11" cy="11" r="6.5" fill="none" stroke="var(--brand-green)" stroke-width="1.5"/><path d="M4.5 11h13M11 4.5c-3 3.5-3 9.5 0 13M11 4.5c3 3.5 3 9.5 0 13" fill="none" stroke="var(--brand-green)" stroke-width="1.2"/></svg>
      </p>
    </div>
  </article>
</main>
</body>
</html>
```